Design a web site for my business - Brightline Coatings Co.

We are a family business that handles design, fabrication and installation of powder coated aluminum, stainless steel and glass products. Including handrails, privacy slat screens, electric gates and pool fencing. We are based in the Whitsundays in North Queensland and service an area from Airlie Beach to Townsville.

Target Market(s)

Domestic and commercial

Industry/Entity Type

fabrication - manufacturing

Coding

Coded - Design and coding required

Number of Pages Required

5+ page

Colors
0054AA
0677BA
7BADD7
CADEEF
E8F1F8

Requirements
Must have
• photo galleries, contact page, one page for privacy screens, balustrades, glass fencing, stainless steel handrail, powder coated aluminium handrails and pool fencing

```html
<!DOCTYPE html>
<html lang="en">
<head>
<meta charset="utf-8">
<title>Brightline Coatings Co — Website Pages</title>
<link href="https://fonts.googleapis.com/css2?family=Inter:wght@400;500;600;700&display=swap" rel="stylesheet">
<style>
:root{
  --board:#262626;
  --paper:#f8f7f5;
  --white:#ffffff;
  --panel:#eeedeb;
  --ink:#0b1222;
  --navy:#050b1c;
  --cta:#0a1a3c;
  --muted:#6b7078;
  --line:#dcdad6;
  --foot-text:#7f8899;
  --foot-link:#4f6aa0;
  --brand:#0054AA;
}
*{box-sizing:border-box;margin:0;padding:0}
html,body{width:989px;height:1200px;overflow:hidden}
body{background:var(--board);font-family:"Inter",sans-serif;color:var(--ink);position:relative}
.page{position:absolute;background:var(--paper);overflow:hidden}
.page-home{left:20px;top:21px;width:298px;height:1158px}
.page-services{left:331px;top:21px;width:313px;height:815px}
.page-projects{left:657px;top:21px;width:313px;height:640px}
.a{position:absolute}
.photo{position:absolute;border-radius:1px}
.nav{position:absolute;left:0;top:0;width:100%;height:19px;background:var(--white);border-bottom:1px solid var(--line)}
.logo{position:absolute;left:14px;top:6px;font-size:5.6px;font-weight:700;letter-spacing:-.05px}
.nav-links{position:absolute;top:7px;display:flex;gap:7px;font-size:3.6px;color:var(--muted)}
.nav-links .on{color:var(--ink);font-weight:600;border-bottom:.6px solid var(--ink);padding-bottom:1px}
.btn-dark{position:absolute;background:var(--ink);color:#fff;font-size:3.6px;font-weight:600;display:flex;align-items:center;justify-content:center}
.btn-light{position:absolute;background:#fff;color:var(--ink);font-size:3.6px;font-weight:600;display:flex;align-items:center;justify-content:center;border:.5px solid var(--line)}
.eyebrow{font-size:2.6px;font-weight:600;letter-spacing:.3px;text-transform:uppercase;color:var(--muted)}
.h2{font-weight:600;letter-spacing:-.1px}
.small{font-size:3.3px;line-height:1.45;color:var(--muted)}
.card{position:absolute;background:#fff;border:.5px solid var(--line)}
.card-title{font-size:5.2px;font-weight:500;margin-bottom:3px}
.link{font-size:3.3px;font-weight:600}
.icon-sq{position:absolute;width:10px;height:10px;background:var(--ink);display:flex;align-items:center;justify-content:center}
.feat-title{font-size:3.5px;font-weight:600;margin-bottom:2px}
.footer{position:absolute;left:0;width:100%;background:var(--navy);color:#fff}
.foot-logo{position:absolute;left:15px;font-size:5.8px;font-weight:700;line-height:1.2}
.foot-col{position:absolute}
.foot-col h4{font-size:3.2px;font-weight:600;margin-bottom:4px}
.foot-col p{font-size:3.2px;color:var(--foot-text);margin-bottom:4.5px}
.foot-bottom{position:absolute;left:15px;right:15px;display:flex;justify-content:space-between;font-size:2.9px;color:var(--foot-text)}
.chip{font-size:2.8px;border:.5px solid #d5d3cf;border-radius:2px;padding:1.5px 3px;background:#fff}
.input{background:#fff;border:.5px solid #cfcdc9;font-size:3.2px;color:#999;padding:3px}
.lbl{font-size:2.4px;font-weight:600;color:var(--muted);letter-spacing:.2px;margin-bottom:2px}
.quote{position:absolute;width:70px;text-align:center;font-size:4.2px;line-height:1.5}
.quote .who{font-size:3px;font-weight:600;margin-top:6px}
.qmark{position:absolute;font-size:16px;color:#c9c9c9;font-family:Georgia,serif;line-height:1}
.step{position:absolute;width:60px;text-align:center}
.step .ico{width:21px;height:21px;background:var(--ink);margin:0 auto 4px;display:flex;align-items:center;justify-content:center}
.step h5{font-size:6px;font-weight:600;margin-bottom:2px}
.step p{font-size:3px;color:var(--muted);line-height:1.4}
.filter{font-size:3.4px;border:.5px solid #bdbbb7;border-radius:2px;padding:0 6px;height:10px;display:flex;align-items:center;background:#fff}
.filter.on{background:var(--ink);color:#fff;border-color:var(--ink)}
</style>
</head>
<body>

<!-- ============ HOME PAGE ============ -->
<section class="page page-home">
  <header class="nav">
    <div class="logo">Brightline Coatings Co</div>
    <nav class="nav-links" style="left:115px"><span class="on">Services</span><span>Projects</span><span>Areas</span><span>About</span><span>Contact</span></nav>
    <div class="btn-dark" style="left:245px;top:4px;width:38px;height:11px">Request Quote</div>
  </header>

  <div class="photo" role="img" aria-label="Coastal hillside home with glass balustrade deck and pool overlooking island waters" style="left:0;top:19px;width:298px;height:203px;background:linear-gradient(180deg,#8fb3cf 0%,#b9cfdf 22%,#3f8fa8 40%,#2a7894 55%,#6f7e86 75%,#a8acaf 100%)"></div>
  <div class="a" style="left:0;top:19px;width:200px;height:203px;background:linear-gradient(90deg,rgba(5,12,28,.55),rgba(5,12,28,0))"></div>
  <h1 class="a" style="left:15px;top:81px;width:150px;color:#fff;font-size:11.2px;font-weight:600;line-height:1.17;letter-spacing:-.2px">Precision Fabrication &amp; Professional Installation in the Whitsundays</h1>
  <p class="a" style="left:15px;top:126px;width:140px;color:#e7ecf2;font-size:3.8px;line-height:1.5">Family-owned and operated, delivering premium aluminum, stainless steel, and glass solutions from Airlie Beach to Townsville.</p>
  <div class="btn-light" style="left:15px;top:147px;width:58px;height:13px;border:none">Request a Free Quote →</div>
  <div class="a" style="left:78px;top:147px;width:58px;height:13px;border:.5px solid rgba(255,255,255,.7);color:#fff;font-size:3.6px;font-weight:600;display:flex;align-items:center;justify-content:center">View Recent Projects</div>

  <div class="a eyebrow" style="left:0;width:298px;top:244px;text-align:center;color:var(--ink)">Our Expertise</div>
  <h2 class="a h2" style="left:0;width:298px;top:251px;text-align:center;font-size:7.4px">High-End Solutions for Modern Living</h2>

  <div class="card" style="left:15px;top:274px;width:63px;height:120px">
    <div class="photo" role="img" aria-label="Brushed stainless handrail bracket on concrete wall" style="left:2px;top:2px;width:59px;height:59px;background:linear-gradient(135deg,#9a9a98,#c6c5c2 60%,#8a8986)"></div>
    <div class="a" style="left:5px;top:67px;width:54px"><div class="card-title">Handrails</div><p class="small">Durable stainless steel and aluminum handrails designed for safety and architectural elegance.</p><div class="link" style="margin-top:4px">Learn More →</div></div>
  </div>
  <div class="card" style="left:83.5px;top:274px;width:63px;height:120px">
    <div class="photo" role="img" aria-label="Dark aluminium slat privacy screen on tropical patio" style="left:2px;top:2px;width:59px;height:59px;background:linear-gradient(135deg,#4f7a4a,#2d2f2f 55%,#a89c88)"></div>
    <div class="a" style="left:5px;top:67px;width:54px"><div class="card-title">Privacy Screens</div><p class="small">Elegant slat screening solutions that provide privacy without compromising on airflow or aesthetics.</p><div class="link" style="margin-top:4px">Learn More →</div></div>
  </div>
  <div class="card" style="left:152px;top:274px;width:63px;height:120px">
    <div class="photo" role="img" aria-label="Timber-look electric sliding gate at modern home driveway" style="left:2px;top:2px;width:59px;height:59px;background:linear-gradient(135deg,#9fb9cc,#8a5c3a 50%,#b7b2aa)"></div>
    <div class="a" style="left:5px;top:67px;width:54px"><div class="card-title">Electric Gates</div><p class="small">Secure and sophisticated automated gate systems custom-built for residential and commercial entries.</p><div class="link" style="margin-top:4px">Learn More →</div></div>
  </div>
  <div class="card" style="left:220.5px;top:274px;width:63px;height:120px">
    <div class="photo" role="img" aria-label="Frameless glass pool fence beside ocean view pool" style="left:2px;top:2px;width:59px;height:59px;background:linear-gradient(180deg,#a9c8de,#4ca5c2 50%,#7fc5d6)"></div>
    <div class="a" style="left:5px;top:67px;width:54px"><div class="card-title">Pool Fencing</div><p class="small">Frameless glass and aluminum pool fencing that meets all safety standards with a high-end finish.</p><div class="link" style="margin-top:4px">Learn More →</div></div>
  </div>

  <div class="a" style="left:0;top:417px;width:298px;height:203px;background:var(--panel)"></div>
  <h2 class="a h2" style="left:15px;top:444px;width:125px;font-size:7.4px;line-height:1.25">Built for the Coast, Engineered for Excellence</h2>
  <p class="a small" style="left:15px;top:468px;width:122px;font-size:3.7px">We combine decades of metalwork experience with a deep understanding of North Queensland's unique environmental challenges.</p>
  <div class="icon-sq" style="left:15px;top:499px"><svg width="5" height="5" viewBox="0 0 10 10"><path d="M5 1 2 9M5 1l3 8" stroke="#fff" stroke-width="1.2" fill="none"/></svg></div>
  <div class="a" style="left:15px;top:513px;width:58px"><div class="feat-title">Custom Fabrication</div><p class="small">Every project is custom-measured and built in our workshop to your exact specifications.</p></div>
  <div class="icon-sq" style="left:82px;top:499px"><svg width="5" height="5" viewBox="0 0 10 10"><circle cx="5" cy="5" r="4" fill="#fff"/><path d="M3 5l1.5 1.5L7 4" stroke="#0b1222" stroke-width="1.2" fill="none"/></svg></div>
  <div class="a" style="left:82px;top:513px;width:58px"><div class="feat-title">Premium Materials</div><p class="small">We only use marine-grade stainless steel and high-tensile aluminum suited for coastal salt air.</p></div>
  <div class="icon-sq" style="left:15px;top:553px"><svg width="5" height="5" viewBox="0 0 10 10"><circle cx="4" cy="4" r="2" fill="#fff"/><path d="M1 9c0-2 2-3 3-3s3 1 3 3" fill="#fff"/></svg></div>
  <div class="a" style="left:15px;top:567px;width:58px"><div class="feat-title">Professional Installation</div><p class="small">Our trade-qualified team ensures every installation is structurally sound and perfectly finished.</p></div>
  <div class="icon-sq" style="left:82px;top:553px"><svg width="5" height="5" viewBox="0 0 10 10"><path d="M5 9C2 6 2 4 2 4a3 3 0 0 1 6 0s0 2-3 5z" fill="#fff"/><circle cx="5" cy="4" r="1" fill="#0b1222"/></svg></div>
  <div class="a" style="left:82px;top:567px;width:58px"><div class="feat-title">NQ Specialists</div><p class="small">Proudly serving Bowen, Airlie Beach, and Townsville with localized expert service.</p></div>
  <div class="photo" role="img" aria-label="Welder in protective gear working on steel in the workshop" style="left:156px;top:439px;width:127px;height:158px;background:linear-gradient(150deg,#6d7478,#3a4a66 45%,#9bb7e6 60%,#2b3444)"></div>
  <div class="a" style="left:151px;top:571px;width:47px;height:32px;background:#fff;box-shadow:0 1px 3px rgba(0,0,0,.12)">
    <div style="position:absolute;left:7px;top:6px;font-size:11px;font-weight:600">25+</div>
    <div style="position:absolute;left:7px;top:21px;font-size:2.4px;font-weight:600;letter-spacing:.2px;color:var(--muted)">YEARS EXPERIENCE</div>
  </div>

  <h2 class="a h2" style="left:15px;top:643px;font-size:7.4px">Recent Installations</h2>
  <p class="a small" style="left:15px;top:654px">Explore our portfolio of commercial and residential work across the Whitsundays.</p>
  <div class="a link" style="left:249px;top:653px;border-bottom:.5px solid var(--ink)">View Full Gallery →</div>
  <div class="photo" role="img" aria-label="Curved glass balcony above turquoise bay" style="left:15px;top:671px;width:86px;height:64px;background:linear-gradient(160deg,#8fc3dd,#1f8fb8 55%,#c9d3d8)"></div>
  <div class="photo" role="img" aria-label="Black steel staircase in commercial foyer" style="left:106px;top:671px;width:86px;height:64px;background:linear-gradient(160deg,#c9c9c7,#6b6e70 50%,#b1b1ae)"></div>
  <div class="photo" role="img" aria-label="Laser-cut decorative gate at modern home" style="left:197px;top:671px;width:86px;height:64px;background:linear-gradient(160deg,#dfe6ea,#a99883 50%,#5a4a3a)"></div>

  <div class="a" style="left:0;top:758px;width:298px;height:110px;background:var(--white)"></div>
  <h2 class="a h2" style="left:0;width:298px;top:781px;text-align:center;font-size:7.4px">Real Feedback from Local Clients</h2>
  <div class="qmark" style="left:15px;top:801px">❞</div>
  <div class="quote" style="left:20px;top:806px">"The quality of the glass balustrade Brightline Coatings Co installed on our deck is absolutely world-class. It transformed our view and feels incredibly solid."<div class="who">— Owen R., Airlie Beach</div></div>
  <div class="qmark" style="left:108px;top:801px">❞</div>
  <div class="quote" style="left:113px;top:806px">"Professional, on time, and the electric gate works perfectly. The custom design they did for our front fence is the talk of the street."<div class="who">— Priya K., Townsville</div></div>
  <div class="qmark" style="left:201px;top:801px">❞</div>
  <div class="quote" style="left:206px;top:806px">"From the first quote to the final installation, the communication was excellent. They handled the whole process with true NQ craftsmanship."<div class="who">— Lachlan B., Bowen</div></div>

  <div class="a" style="left:15px;top:886px;width:268px;height:150px;background:var(--panel)"></div>
  <h2 class="a h2" style="left:30px;top:903px;font-size:7.4px">Let's Discuss Your Project</h2>
  <p class="a small" style="left:30px;top:918px;width:110px;font-size:3.7px">Ready to upgrade your home or business? Fill out the form and our team will get back to you within 24 hours for a free site measure and quote.</p>
  <div class="a" style="left:30px;top:946px;display:flex;flex-direction:column;gap:7px;font-size:3.6px;font-weight:600">
    <div style="display:flex;align-items:center;gap:5px"><svg width="8" height="8" viewBox="0 0 10 10"><circle cx="5" cy="5" r="5" fill="#fff"/><path d="M3.3 2.8c0 2.2 1.7 4 3.9 4l.5-1-1.2-.6-.5.5c-.8-.4-1.4-1-1.8-1.8l.5-.5-.6-1.2z" fill="#0b1222"/></svg>04XX XXX XXX</div>
    <div style="display:flex;align-items:center;gap:5px"><svg width="8" height="8" viewBox="0 0 10 10"><circle cx="5" cy="5" r="5" fill="#fff"/><rect x="2.7" y="3.3" width="4.6" height="3.4" fill="none" stroke="#0b1222" stroke-width=".6"/><path d="M2.7 3.3 5 5.2l2.3-1.9" stroke="#0b1222" stroke-width=".6" fill="none"/></svg>hello@brightlinecoatings.example</div>
    <div style="display:flex;align-items:center;gap:5px"><svg width="8" height="8" viewBox="0 0 10 10"><circle cx="5" cy="5" r="5" fill="#fff"/><path d="M5 8C3.3 6.2 3.2 5 3.2 4.4a1.8 1.8 0 0 1 3.6 0C6.8 5 6.7 6.2 5 8z" fill="none" stroke="#0b1222" stroke-width=".6"/></svg>Airlie Beach &amp; Bowen Workshops</div>
  </div>
  <div class="a" style="left:156px;top:901px;width:112px;height:120px;background:#fff;padding:8px 7px">
    <div style="display:flex;gap:5px">
      <div style="flex:1"><div class="lbl">FULL NAME</div><div class="input">John Smith</div></div>
      <div style="flex:1"><div class="lbl">PHONE NUMBER</div><div class="input">0400 000 000</div></div>
    </div>
    <div class="lbl" style="margin-top:7px">SERVICE REQUIRED</div>
    <div class="input" style="color:var(--ink);display:flex;justify-content:space-between">Handrails / Balustrades<span>⌄</span></div>
    <div class="lbl" style="margin-top:7px">MESSAGE</div>
    <div class="input" style="height:29px">Tell us about your project...</div>
    <div class="btn-dark" style="position:relative;margin-top:7px;height:13px">Send Enquiry</div>
  </div>

  <footer class="footer" style="top:1053px;height:105px">
    <div class="foot-logo" style="top:15px">Brightline<br>Coatings Co</div>
    <p class="a" style="left:15px;top:37px;width:57px;font-size:3.2px;line-height:1.5;color:#b8bfcc">Precision Craftsmanship for the Coast. Your local partners in architectural metal and glass.</p>
    <div class="foot-col" style="left:83px;top:14px"><h4 style="font-size:2.6px;letter-spacing:.3px">SERVICES</h4><p style="color:#b8bfcc">Handrails</p><p style="color:#b8bfcc">Privacy Screens</p><p style="color:#b8bfcc">Electric Gates</p><p style="color:#b8bfcc">Pool Fencing</p><p style="color:#b8bfcc">Glass Balustrades</p></div>
    <div class="foot-col" style="left:151px;top:14px"><h4 style="font-size:2.6px;letter-spacing:.3px">AREAS SERVED</h4><p style="color:#b8bfcc">Airlie Beach</p><p style="color:#b8bfcc">Bowen</p><p style="color:#b8bfcc">Cannonvale</p><p style="color:#b8bfcc">Proserpine</p><p style="color:#b8bfcc">Townsville</p></div>
    <div class="foot-col" style="left:220px;top:14px;width:64px"><h4 style="font-size:2.6px;letter-spacing:.3px">CONTACT</h4><p style="color:#b8bfcc;line-height:1.5">Available Mon-Fri 7:00 AM - 5:00 PM</p></div>
    <div class="btn-light" style="left:220px;top:39px;width:38px;height:9px;border:none">Request Quote</div>
    <div class="foot-bottom" style="top:88px"><span>© 2024 Brightline Coatings Co. Precision Craftsmanship for the Coast.</span><span>Privacy Policy &nbsp;&nbsp; Terms of Service</span></div>
  </footer>
</section>

<!-- ============ SERVICES PAGE ============ -->
<section class="page page-services">
  <header class="nav">
    <div class="logo" style="left:16px">Brightline Coatings Co</div>
    <nav class="nav-links" style="left:121px"><span class="on">Services</span><span>Projects</span><span>Areas</span><span>About</span><span>Contact</span></nav>
    <div class="btn-dark" style="left:257px;top:4px;width:40px;height:11px">Request Quote</div>
  </header>
  <div class="a" style="left:0;top:19px;width:313px;height:150px;background:var(--white)"></div>
  <div class="a" style="left:15px;top:52px;background:var(--cta);color:#8fb4ea;font-size:2.4px;font-weight:600;padding:1px 3px;letter-spacing:.2px">PREMIUM CRAFTSMANSHIP</div>
  <h1 class="a" style="left:15px;top:63px;width:120px;font-size:12.2px;font-weight:600;line-height:1.12;letter-spacing:-.2px">Expert Fabrication Services</h1>
  <p class="a small" style="left:15px;top:97px;width:127px;font-size:3.9px">Precision-engineered aluminum and steel solutions for high-end coastal properties. We balance industrial strength with architectural elegance.</p>
  <div class="btn-dark" style="left:15px;top:124px;width:49px;height:14px">Explore Solutions</div>
  <div class="btn-light" style="left:68px;top:124px;width:40px;height:14px">View Gallery</div>
  <div class="photo" role="img" aria-label="Stainless glass balustrade post on balcony above island bay" style="left:162px;top:46px;width:135px;height:98px;background:linear-gradient(170deg,#a5c7de,#2b90b6 45%,#5a7f88 80%,#b5b2ad);box-shadow:0 2px 5px rgba(0,0,0,.12)"></div>

  <div class="card" style="left:15px;top:193px;width:138px;height:96px"></div>
  <div class="a" style="left:23px;top:202px;width:76px">
    <div class="card-title" style="font-size:7px;line-height:1.15">Handrails &amp; Balustrades</div>
    <p class="small">Combining marine-grade stainless steel with architectural glass for safety that doesn't compromise your view.</p>
    <div style="display:flex;flex-wrap:wrap;gap:3px;margin-top:4px"><span class="chip">⊙ Durability</span><span class="chip">✦ Style</span><span class="chip">⌂ Low Maintenance</span></div>
    <div class="link" style="margin-top:9px;display:inline-block;border-bottom:.5px solid var(--ink)">View Project Gallery →</div>
  </div>
  <div class="photo" role="img" aria-label="Frameless glass balustrade on white terrace" style="left:112px;top:201px;width:81px;height:79px;background:linear-gradient(160deg,#bcd6e6,#e9eef1 50%,#9fb7c4)"></div>
  <div class="a" style="left:207px;top:193px;width:90px;height:96px;background:var(--ink);color:#fff;padding:8px">
    <div style="font-size:6px;font-weight:500;margin-bottom:4px">Privacy Slat Screens</div>
    <p style="font-size:3.3px;line-height:1.45;color:#b8bfcc">Powder-coated aluminum solutions designed for optimal airflow and visual seclusion.</p>
    <div style="font-size:3.4px;margin-top:5px;line-height:2.5">◎ Weather Resistant<br>◎ Custom Color Match<br>◎ Lightweight Alloy</div>
    <div class="btn-light" style="left:8px;top:74px;width:74px;height:13px;border:none">View Gallery</div>
  </div>

  <div class="card" style="left:15px;top:295px;width:138px;height:144px"></div>
  <div class="photo" role="img" aria-label="Dark slatted driveway gate with stone wall and palms" style="left:15px;top:295px;width:138px;height:63px;background:linear-gradient(180deg,#9ebbd2,#5f7d4c 45%,#3a3b3a 70%,#9a9287)"></div>
  <div class="a" style="left:23px;top:366px;width:124px">
    <div class="card-title" style="font-size:7px">Electric &amp; Manual Gates</div>
    <p class="small">Sophisticated entry systems featuring high-torque automation for effortless security.</p>
    <div style="display:flex;gap:3px;margin-top:5px">
      <div style="flex:1;background:#f3f2ef;padding:3px 4px;font-size:3.4px;font-weight:600">Durability<div style="font-size:2.8px;font-weight:400;color:var(--muted)">Industrial Grade</div></div>
      <div style="flex:1;background:#f3f2ef;padding:3px 4px;font-size:3.4px;font-weight:600">Security<div style="font-size:2.8px;font-weight:400;color:var(--muted)">Smart Access</div></div>
    </div>
    <div class="btn-dark" style="position:relative;margin-top:6px;height:12px">View Project Gallery</div>
  </div>
  <div class="card" style="left:160px;top:295px;width:138px;height:144px"></div>
  <div class="a" style="left:168px;top:326px;width:56px">
    <div class="card-title" style="font-size:7px">Pool Fencing</div>
    <p class="small">Compliant, crystal-clear glass or aluminum tube fencing that protects your family while enhancing the poolside aesthetic.</p>
    <div style="font-size:3.4px;margin-top:5px;line-height:1.7">⛉ Safety Standard Certified<br>◔ Custom Powder Coating</div>
    <div class="link" style="margin-top:6px">View Gallery →</div>
  </div>
  <div class="photo" role="img" aria-label="Glass pool fence beside bright blue pool and palms" style="left:229px;top:295px;width:69px;height:144px;background:linear-gradient(180deg,#6fa67a,#9fcfe0 30%,#2ea3cf 60%,#60c0df)"></div>

  <div class="a" style="left:0;top:459px;width:313px;height:146px;background:var(--white)"></div>
  <div class="a eyebrow" style="left:0;width:313px;top:489px;text-align:center">Our Methodology</div>
  <h2 class="a h2" style="left:0;width:313px;top:496px;text-align:center;font-size:12.2px">Precision From Start to Finish</h2>
  <div class="a" style="left:15px;top:537px;width:282px;height:.6px;background:var(--line)"></div>
  <div class="step" style="left:18px;top:527px"><div class="ico"><svg width="9" height="9" viewBox="0 0 10 10"><path d="M5 1 9 5 5 9 1 5z" fill="none" stroke="#fff" stroke-width="1"/></svg></div><h5>Consultation</h5><p>On-site measurement and requirements analysis for your specific coastal environment.</p></div>
  <div class="step" style="left:90px;top:527px"><div class="ico"><svg width="9" height="9" viewBox="0 0 10 10"><path d="M5 1 2.5 9M5 1l2.5 8" stroke="#fff" stroke-width="1" fill="none"/></svg></div><h5>Design</h5><p>Detailed 3D modelling and material selection to ensure architectural harmony.</p></div>
  <div class="step" style="left:162px;top:527px"><div class="ico"><svg width="9" height="9" viewBox="0 0 10 10"><path d="M2 9h6M3 9V5l3-3 2 2" stroke="#fff" stroke-width="1" fill="none"/></svg></div><h5>Fabrication</h5><p>Workshop crafting using high-grade materials and precision welding techniques.</p></div>
  <div class="step" style="left:234px;top:527px"><div class="ico"><svg width="9" height="9" viewBox="0 0 10 10"><path d="M2 8l6-6M2 2l6 6" stroke="#fff" stroke-width="1.1"/></svg></div><h5>Installation</h5><p>Expert on-site fitting with attention to structural integrity and finishing details.</p></div>

  <div class="a" style="left:15px;top:624px;width:282px;height:50px;background:var(--cta);border-radius:2px">
    <div style="position:absolute;left:12px;top:12px;color:#fff;font-size:7.6px;font-weight:600">Ready to elevate your property?</div>
    <div style="position:absolute;left:12px;top:25px;width:125px;color:#c5d3ea;font-size:3.9px;line-height:1.5">Contact us for a free on-site consultation and quote in the Whitsunday region.</div>
    <div class="btn-light" style="left:168px;top:17px;width:55px;height:17px;border:none">Request a Quote</div>
    <div class="a" style="left:226px;top:17px;width:44px;height:17px;border:.5px solid #44577c;color:#fff;font-size:3.6px;font-weight:600;display:flex;align-items:center;justify-content:center">Contact Us</div>
  </div>

  <footer class="footer" style="top:718px;height:97px">
    <div class="foot-logo" style="top:13px">Brightline<br>Coatings Co</div>
    <p class="a" style="left:15px;top:32px;width:60px;font-size:3.4px;line-height:1.5;color:#b8bfcc">Precision Craftsmanship for the Coast.</p>
    <div class="a" style="left:15px;top:46px;display:flex;gap:4px"><svg width="9" height="9" viewBox="0 0 10 10"><circle cx="5" cy="5" r="4.5" fill="none" stroke="#fff" stroke-width=".5"/><circle cx="5" cy="5" r="2" fill="none" stroke="#fff" stroke-width=".6"/></svg><svg width="9" height="9" viewBox="0 0 10 10"><circle cx="5" cy="5" r="4.5" fill="none" stroke="#fff" stroke-width=".5"/><rect x="3" y="3.5" width="4" height="3" fill="none" stroke="#fff" stroke-width=".5"/></svg></div>
    <div class="foot-col" style="left:88px;top:13px"><h4>Our Services</h4><p style="color:var(--foot-link)">Handrails</p><p style="color:var(--foot-link)">Privacy Screens</p><p style="color:var(--foot-link)">Electric Gates</p><p style="color:var(--foot-link)">Pool Fencing</p></div>
    <div class="foot-col" style="left:160px;top:13px"><h4>More</h4><p style="color:var(--foot-link)">Glass Balustrades</p><p style="color:var(--foot-link)">Custom Fabrication</p></div>
    <div class="foot-col" style="left:232px;top:13px"><h4>Service Areas</h4><p style="color:var(--foot-link)">Airlie Beach</p><p style="color:var(--foot-link)">Bowen</p><p style="color:var(--foot-link)">Townsville</p></div>
    <div class="foot-bottom" style="top:81px"><span>© 2024 Brightline Coatings Co. Precision Craftsmanship for the Coast.</span><span>Privacy Policy &nbsp;&nbsp; Terms of Service</span></div>
  </footer>
</section>

<!-- ============ PROJECTS PAGE ============ -->
<section class="page page-projects">
  <header class="nav">
    <div class="logo" style="left:16px">Brightline Coatings Co</div>
    <nav class="nav-links" style="left:121px"><span>Services</span><span class="on">Projects</span><span>Areas</span><span>About</span><span>Contact</span></nav>
    <div class="btn-dark" style="left:257px;top:4px;width:40px;height:11px">Request Quote</div>
  </header>
  <div class="a eyebrow" style="left:15px;top:36px;color:var(--ink)">Precision Built</div>
  <h1 class="a" style="left:15px;top:43px;font-size:12.2px;font-weight:600;letter-spacing:-.2px">Our Craftsmanship in Action</h1>
  <p class="a small" style="left:15px;top:63px;width:170px;font-size:3.9px">Explore our portfolio of high-end architectural metalwork, glass installations, and custom fabrication projects across North Queensland.</p>
  <div class="a" style="left:15px;top:88px;display:flex;gap:4px"><span class="filter on">All Projects</span><span class="filter">Handrails</span><span class="filter">Gates</span><span class="filter">Fencing</span><span class="filter">Privacy Screens</span></div>
  <div class="photo" role="img" aria-label="Modern home with glass pool fence and infinity pool above bay" style="left:15px;top:108px;width:186px;height:104px;background:linear-gradient(170deg,#9cc0d8,#5b8662 35%,#2fa6d0 60%,#68c2dd)"></div>
  <div class="photo" role="img" aria-label="Silver aluminium slat gate at commercial building" style="left:207px;top:108px;width:90px;height:104px;background:linear-gradient(160deg,#c7d3dc,#9ea3a6 50%,#5d5f60)"></div>
  <div class="photo" role="img" aria-label="Outdoor stairway with steel handrail down to the coast" style="left:15px;top:219px;width:90px;height:90px;background:linear-gradient(170deg,#c9d1d4,#7d8b7a 45%,#a8a399)"></div>
  <div class="photo" role="img" aria-label="Laser-cut decorative screen on timber deck at sunset" style="left:111px;top:219px;width:90px;height:90px;background:linear-gradient(160deg,#d9b47e,#4a3b2d 50%,#7d5a3a)"></div>
  <div class="photo" role="img" aria-label="Marina boardwalk with stainless railing and moored boats" style="left:207px;top:219px;width:90px;height:90px;background:linear-gradient(180deg,#a9c9df,#4d9fc2 50%,#7a6a58)"></div>
  <div class="photo" role="img" aria-label="Lit black steel entrance gate between stone pillars at dusk" style="left:15px;top:315px;width:282px;height:120px;background:linear-gradient(180deg,#33465f,#5a6878 40%,#3b3a36 75%,#6b6a62)"></div>

  <div class="a" style="left:15px;top:459px;width:282px;height:84px;background:var(--ink);border-radius:1px;text-align:center">
    <div style="margin-top:13px;color:#fff;font-size:7.6px;font-weight:600">Ready to start your project?</div>
    <div style="margin:5px auto 0;width:135px;color:#8ea3c4;font-size:3.9px;line-height:1.5">Whether it's a bespoke residential build or a large-scale commercial installation, our team is ready to bring your vision to life.</div>
    <div class="btn-light" style="left:113px;top:57px;width:55px;height:14px;border:none">Request a Quote</div>
  </div>

  <footer class="footer" style="top:560px;height:80px">
    <div class="foot-logo" style="top:13px">Brightline<br>Coatings Co</div>
    <p class="a" style="left:15px;top:33px;width:60px;font-size:3.2px;line-height:1.5;color:var(--foot-text)">© 2024 Brightline Coatings Co. Precision Craftsmanship for the Coast.</p>
    <div class="foot-col" style="left:87px;top:13px"><h4>Services</h4><p style="color:var(--foot-link)">Handrails</p><p style="color:var(--foot-link)">Privacy Screens</p><p style="color:var(--foot-link)">Electric Gates</p><p style="color:var(--foot-link)">Pool Fencing</p><p style="color:var(--foot-link)">Glass Balustrades</p></div>
    <div class="foot-col" style="left:159px;top:13px"><h4>Areas</h4><p style="color:var(--foot-link)">Airlie Beach</p><p style="color:var(--foot-link)">Bowen</p><p style="color:var(--foot-link)">Townsville</p><p style="color:var(--foot-link)">Custom Fabrication</p></div>
    <div class="foot-col" style="left:232px;top:13px"><h4>Connect</h4>
      <div style="display:flex;gap:6px;margin:3px 0 7px"><svg width="8" height="8" viewBox="0 0 10 10"><circle cx="7" cy="2.5" r="1.2" fill="#fff"/><circle cx="2.5" cy="5" r="1.2" fill="#fff"/><circle cx="7" cy="7.5" r="1.2" fill="#fff"/><path d="M7 2.5 2.5 5 7 7.5" stroke="#fff" stroke-width=".6" fill="none"/></svg><svg width="8" height="8" viewBox="0 0 10 10"><rect x="1.5" y="2.5" width="7" height="5" fill="none" stroke="#fff" stroke-width=".7"/><path d="M1.5 2.5 5 5.3l3.5-2.8" stroke="#fff" stroke-width=".7" fill="none"/></svg></div>
      <p style="font-size:2.9px;line-height:1.3">48 Harbour Works Rd,<br>Cannonvale, QLD</p></div>
  </footer>
</section>

</body>
</html>
```